Zielgruppe
Produtkion von Bioeiern. Wir suchen ein Design für eine Eierpappe. Im Focus stehen die Aspekte Regionalität und Bio
Zielgruppe: Endverbraucher
Aufgabenstellung
Nicht zu bunt eher natur und bodenständig.
Es müssen diverse Sigel (Eu -Bio, Verbandlogo und VRN-Sigel) und EAN auf die Pappe.
Es handelt sich um 6er Pappen und 10er Pappen
Vielleicht gibt es auch Vorschläge zu neuen Verpackungen, also nicht die standrad-Eierpappe....
Nicht unbedingt ein Foto mit dem Huhn auf der grünen Wiese. eher in die Richtung Kartoon oder Karikatur.

```html
<!DOCTYPE html>
<html lang="de">
<head>
<meta charset="utf-8">
<title>Bio Eier – Etikett 6er Pappe</title>
<link rel="stylesheet" href="https://fonts.googleapis.com/css2?family=Kaushan+Script&family=Open+Sans:wght@400;600&family=Lora:ital,wght@1,500&display=swap">
<style>
  :root {
    --page-bg: #f4f4f1;
    --label-green: #1f5a34;
    --label-beige: #cbbfac;
    --bio-green: #2f6e3c;
    --text-light: #ffffff;
    --text-dark: #1d4a2b;
    --eu-green: #8cc63f;
    --seal-white: #ffffff;
    --seal-red: #c8312b;
    --cutout: #e6e8df;
  }
  * { margin: 0; padding: 0; box-sizing: border-box; }
  html, body { width: 1200px; height: 829px; overflow: hidden; }
  body { background: var(--page-bg); position: relative; font-family: "Open Sans", sans-serif; }

  .carton-label {
    position: absolute;
    left: 450px; top: 20px;
    width: 300px; height: 790px;
    background: var(--label-green);
    overflow: hidden;
  }
  .mascot {
    position: absolute;
    left: 40px; top: 8px;
    width: 240px; height: 160px;
    border-radius: 50%;
    background: radial-gradient(circle at 55% 45%, #ffffff 0%, #f1ece3 45%, var(--label-beige) 100%);
  }
  .product-badge {
    position: absolute;
    left: 55px; top: 136px;
    width: 124px; height: 106px;
    border-radius: 50%;
    background: var(--label-beige);
    text-align: center;
  }
  .product-badge .bio {
    display: block;
    font-family: "Kaushan Script", cursive;
    font-size: 44px;
    line-height: 1;
    color: var(--bio-green);
    margin-top: 10px;
  }
  .product-badge .eier {
    display: block;
    font-family: "Open Sans", sans-serif;
    font-weight: 600;
    font-size: 30px;
    line-height: 1;
    color: var(--text-dark);
    margin-top: 2px;
  }
  .claim {
    position: absolute;
    left: 40px; top: 272px;
    width: 200px;
    font-family: "Kaushan Script", cursive;
    font-size: 26px;
    line-height: 36px;
    color: var(--text-light);
    text-align: center;
    transform: rotate(-7deg);
  }
  .claim span { display: block; }
  .claim .line-2 { padding-left: 30px; }
  .count {
    position: absolute;
    left: 0; top: 398px;
    width: 300px;
    text-align: center;
    font-family: "Lora", serif;
    font-style: italic;
    font-weight: 500;
    font-size: 22px;
    color: var(--text-light);
  }
  .window-cutout {
    position: absolute;
    left: 86px; top: 456px;
    width: 128px; height: 128px;
    border-radius: 50%;
    background: var(--cutout);
  }
  .address-strip {
    position: absolute;
    left: 112px; top: 592px;
    width: 76px; height: 198px;
    background: var(--label-beige);
    text-align: center;
    padding-top: 28px;
    font-size: 14px;
    line-height: 25px;
    color: var(--text-dark);
  }
  .eu-organic-seal {
    position: absolute;
    left: 33px; top: 628px;
    width: 58px; height: 52px;
    background: var(--eu-green);
  }
  .origin-seal {
    position: absolute;
    left: 206px; top: 623px;
    width: 64px; height: 64px;
    border-radius: 50%;
    background: var(--seal-white);
    border: 5px solid var(--seal-red);
  }
</style>
</head>
<body>
  <div class="carton-label">
    <div class="mascot" role="img" aria-label="Cartoon-Huhn, das den Daumen hebt"></div>

    <div class="product-badge">
      <span class="bio">Bio</span>
      <span class="eier">Eier</span>
    </div>

    <p class="claim">
      <span class="line-1">frisch aus</span>
      <span class="line-2">der Region!</span>
    </p>

    <p class="count">6 Stück</p>

    <div class="window-cutout"></div>

    <div class="address-strip">
      <p>Adr. Betrieb</p>
      <p>PLZ</p>
      <p>Ortschaft</p>
    </div>

    <div class="eu-organic-seal" role="img" aria-label="EU-Bio-Siegel"></div>
    <div class="origin-seal" role="img" aria-label="Herkunftssiegel"></div>
  </div>
</body>
</html>
```